Bramblewood Joinery Website

My client Bramblewood Joinery is looking for a redesign for a Word Press Website. Their current site is at www.bramblewoodjoinery.example They are a custom cabinet company, but also create bathroom, living room, bar and entertainment and bedroom cabinets too. They would like a design that emulates the master craftsman work they do yet a contemporary style.

Their current site was designed using Flash elements.

Target Market(s)

Home owners and builders of high end homes

Industry/Entity Type

Entertainment

Font styles to use
Serif
Decorative

Requirements
Must have
• Must show their work and logo using a contemporary style.
Nice to have
• Sliders that showcase their projects.

```html
<!DOCTYPE html>
<html lang="en">
<head>
<meta charset="utf-8">
<title>Bramblewood Joinery</title>
<link href="https://fonts.googleapis.com/css2?family=Titillium+Web:wght@400;600;700&family=Ubuntu:wght@400;500&display=swap" rel="stylesheet">
<style>
:root{
  --green:#37b13a;
  --green-dark:#2c9a2f;
  --ink:#1e1e1e;
  --text:#5a5a5a;
  --paper:#f3f3f3;
  --white:#ffffff;
  --slate:#555657;
  --wood:#7a4a2a;
  --photo-light:#cfc6b8;
  --photo-dark:#4a3a2e;
}
*{margin:0;padding:0;box-sizing:border-box}
html,body{width:673px;height:1200px;overflow:hidden}
body{position:relative;background:var(--paper) repeating-linear-gradient(45deg,rgba(0,0,0,.018) 0 1px,transparent 1px 3px);font-family:"Ubuntu",sans-serif;color:var(--text)}
.abs{position:absolute}
.topline{left:0;top:0;width:673px;height:3px;background:var(--green)}
.nav{left:64px;top:41px;width:544px;height:37px;background:linear-gradient(var(--green),var(--green-dark))}
.nav a{position:absolute;top:14px;color:var(--white);font:600 7.5px "Titillium Web",sans-serif;text-decoration:none;white-space:nowrap}
.brand{left:296px;top:22px;width:70px;height:70px;border-radius:50%;background:var(--white);display:flex;align-items:center;justify-content:center;text-align:center;font:700 9px/1.15 "Titillium Web",sans-serif;color:var(--green)}
.photo{background:linear-gradient(135deg,var(--photo-light),#8c7f6f 55%,var(--photo-dark))}
.photo.warm{background:linear-gradient(135deg,#c99a5c,var(--wood) 60%,#3e2414)}
.slider{left:64px;top:93px;width:544px;height:284px;background:var(--white);box-shadow:0 1px 3px rgba(0,0,0,.3)}
.slider .photo{position:absolute;left:6px;top:6px;width:533px;height:272px}
.arrow{width:18px;height:18px;border-radius:50%;background:var(--white);box-shadow:0 1px 2px rgba(0,0,0,.4)}
.dots-tab{left:296px;top:358px;width:78px;height:15px;background:var(--white);border-radius:10px 10px 0 0}
.dot{width:7px;height:7px;border-radius:50%;border:1px solid #7ab0c8;background:var(--white)}
.dot.on{background:var(--green);border-color:var(--green)}
h2{font:600 14px "Titillium Web",sans-serif;color:var(--ink)}
.intro{left:64px;top:424px;width:326px;font-size:6.6px;line-height:13.5px}
.more{color:var(--green)}
.video{left:399px;top:388px;width:208px;height:141px;background:var(--white);box-shadow:0 1px 3px rgba(0,0,0,.3)}
.video .photo{position:absolute;left:3px;top:3px;width:202px;height:135px}
.controls{left:7px;top:116px;width:194px;height:17px;background:rgba(20,20,20,.75)}
.card{width:127px;height:171px;background:var(--white);border:1px solid #ddd;border-top:2px solid var(--green)}
.card .photo{height:94px}
.card h3{margin:9px 5px 4px;font:600 8px "Titillium Web",sans-serif;color:var(--ink)}
.card p{margin:0 5px;font-size:6.4px;line-height:10px}
.card .rm{display:block;text-align:right;margin:5px 6px 0;font-size:6.4px;font-style:italic;color:var(--green)}
.banner{left:64px;top:754px;width:544px;height:91px;border-radius:3px;background:linear-gradient(90deg,#6e5848,#8b7565 45%,#4a3a30)}
.banner h2{position:absolute;left:16px;top:12px;font-size:17px;color:var(--white)}
.banner p{position:absolute;left:16px;top:38px;font-size:6.6px;color:var(--white)}
.btn{background:var(--green);color:var(--white);font:600 7px "Titillium Web",sans-serif;display:flex;align-items:center;justify-content:center;border-radius:2px}
.truck{left:308px;top:11px;width:148px;height:65px;border-radius:4px;background:linear-gradient(90deg,#3c8f3d 0 25%,#efe9de 25%,#c7b79f)}
.seal{left:466px;top:13px;width:64px;height:64px;border-radius:50%;background:var(--white);display:flex;align-items:center;justify-content:center;text-align:center;font:700 8px/1.15 "Titillium Web",sans-serif;color:var(--green)}
.tile{top:900px;width:136px;height:100px;padding:10px 7px;color:var(--white)}
.tile h3{font:600 10.5px "Titillium Web",sans-serif;margin-bottom:4px}
.tile p{font:500 6.6px/10.6px "Ubuntu",sans-serif}
.partners{left:54px;top:1055px;width:342px;height:49px;background:var(--white);display:flex;justify-content:space-around;align-items:center}
.badge{width:62px;height:24px;border-radius:3px;background:#d6d9de}
.qc{left:414px;top:1053px;width:190px;font-size:6.8px;line-height:11px;color:#444}
footer{left:0;top:1128px;width:673px;height:72px;background:var(--green);color:var(--white)}
footer nav{position:absolute;left:64px;top:22px;font:400 9.5px "Titillium Web",sans-serif}
footer small{position:absolute;left:64px;top:42px;font-size:6.2px}
.social{top:25px;width:14px;height:14px;border-radius:2px;background:rgba(255,255,255,.85)}
</style>
</head>
<body>
<div class="abs topline"></div>

<header>
  <nav class="abs nav">
    <a style="left:24px">Home</a>
    <a style="left:60px">About Us</a>
    <a style="left:108px">Who We Are</a>
    <a style="left:165px">Getting Started</a>
    <a style="left:309px">Customer Experience</a>
    <a style="left:394px">Professional</a>
    <a style="left:449px">Portfolio</a>
    <a style="left:491px">Contact Us</a>
  </nav>
  <div class="abs brand">Bramblewood<br>Joinery</div>
</header>

<section class="abs slider">
  <div class="photo" role="img" aria-label="White custom kitchen with island, pendant lights and stainless fridge"></div>
  <div class="abs arrow" style="left:17px;top:130px"><svg width="18" height="18"><path d="M10 5 6 9l4 4" fill="none" stroke="#333" stroke-width="1.8"/></svg></div>
  <div class="abs arrow" style="left:509px;top:130px"><svg width="18" height="18"><path d="M8 5l4 4-4 4" fill="none" stroke="#333" stroke-width="1.8"/></svg></div>
</section>
<div class="abs dots-tab">
  <div class="abs dot on" style="left:24px;top:4px"></div>
  <div class="abs dot" style="left:36px;top:4px"></div>
  <div class="abs dot" style="left:48px;top:4px"></div>
</div>

<h2 class="abs" style="left:64px;top:399px">Welcome To Bramblewood Joinery &amp; Fixtures</h2>
<p class="abs intro">Lorem ipsum dolor sit amet, consectetuer adipiscing elit, sed diam nonummy nibh euismod tincidunt ut laoreet dolore magna aliquam erat volutpat. Ut wisi enim ad minim veniam, quis nostrud exerci tation ullamcorper suscipit lobortis nisl ut aliquip ex ea commodo consequat. Lorem ipsum dolor sit amet, consectetuer adipiscing elit, sed diam nonummy nibh euismod tincidunt ut laoreet dolore magna aliquam erat volutpat. Ut wisi enim ad minim veniam, quis nostrud exerci tation suscipit lobortis nisl ut aliquip ex ea commodo consequat. Lorem ipsum dolor sit amet, consectetuer adipiscing elit, sed diam nonummy<br><span class="more">Read more.....</span></p>

<div class="abs video">
  <div class="photo" role="img" aria-label="Video still of a white kitchen with range hood"></div>
  <div class="abs controls">
    <svg width="194" height="17"><path d="M14 4v9l7-4.5z" fill="#fff"/><rect x="45" y="7" width="116" height="3" fill="#888"/><rect x="166" y="5" width="14" height="7" fill="#6fb6e0"/><path d="M184 5h6v6h-6z" fill="none" stroke="#fff"/></svg>
  </div>
</div>

<section>
  <article class="abs card" style="left:64px;top:556px"><div class="photo" role="img" aria-label="Kitchen project"></div><h3>Kitchens</h3><p>Lorem ipsum dolor sit amet, consectetur adipisicing elit. Ullam voluptate, accusamus</p><span class="rm">-Readmore...</span></article>
  <article class="abs card" style="left:203px;top:556px"><div class="photo" role="img" aria-label="Bath project"></div><h3>Bath</h3><p>Lorem ipsum dolor sit amet, consectetur adipisicing elit. Ullam voluptate, accusamus</p><span class="rm">-Readmore...</span></article>
  <article class="abs card" style="left:341px;top:556px"><div class="photo warm" style="background:linear-gradient(135deg,#b8ab98,#3a2c24 60%,#2a1e18)" role="img" aria-label="Office cabinetry project"></div><h3>Office</h3><p>Lorem ipsum dolor sit amet, consectetur adipisicing elit. Ullam voluptate, accusamus</p><span class="rm">-Readmore...</span></article>
  <article class="abs card" style="left:480px;top:556px"><div class="photo" role="img" aria-label="Workshop project"></div><h3>Workshop</h3><p>Lorem ipsum dolor sit amet, consectetur adipisicing elit. Ullam voluptate, accusamus</p><span class="rm">-Readmore...</span></article>
</section>

<section class="abs banner">
  <h2>Bramblewood Joinery</h2>
  <p>Lorem ipsum dolor sit amet, consectetur adipisicing elit. Ullam voluptate, accusamus</p>
  <div class="abs btn" style="left:17px;top:54px;width:57px;height:20px">Click here</div>
  <div class="abs truck" role="img" aria-label="Branded delivery truck with kitchen photos"></div>
  <div class="abs seal">Bramblewood<br>Joinery</div>
</section>

<h2 class="abs" style="left:64px;top:873px">Portfolio</h2>
<div class="abs tile" style="left:64px;background:var(--green)"><h3>Close Windows</h3><p>Lorem ipsum dolor sit amet, consectetuer adipiscing elit, sed diam nonummy nibh euismod tincidunt ut laoreet dolore magna aliquam erat volutpat.<br>Read more..</p></div>
<div class="abs tile photo warm" style="left:200px" role="img" aria-label="Dark wood kitchen with round island"></div>
<div class="abs tile" style="left:336px;background:var(--slate)"><h3>Kitchen Cabinets</h3><p>Lorem ipsum dolor sit amet, consectetuer adipiscing elit, sed diam nonummy nibh euismod tincidunt ut laoreet dolore magna aliquam erat volutpat.<br>Read more..</p></div>
<div class="abs tile photo warm" style="left:472px" role="img" aria-label="Warm wood kitchen cabinets"></div>

<h2 class="abs" style="left:64px;top:1028px">Partners</h2>
<div class="abs" style="left:121px;top:1039px;width:240px;height:1px;background:#bbb"></div>
<div class="abs dot on" style="left:363px;top:1036px"></div>
<div class="abs dot" style="left:372px;top:1036px;border-color:#777"></div>
<div class="abs dot" style="left:381px;top:1036px;border-color:#777"></div>
<div class="abs partners"><div class="badge"></div><div class="badge"></div><div class="badge"></div><div class="badge"></div></div>

<h2 class="abs" style="left:414px;top:1028px">Quick Contact</h2>
<p class="abs qc">Nunc tempus felis vitae urna Vivamus porttitor g purus nisi eleifend libero a tempus libero lectus Nunc tempus felis vitae urna Vivamus</p>
<div class="abs btn" style="left:537px;top:1093px;width:70px;height:20px;font-size:7.5px">CLICK HERE</div>

<footer class="abs">
  <nav>Home &nbsp;|&nbsp; About Us &nbsp;|&nbsp; Serives &nbsp;|&nbsp; Contact Us &nbsp;|&nbsp; Blog</nav>
  <small>© 2015 Company Name &nbsp;All right reserved &nbsp;Term of Use</small>
  <div class="abs social" style="left:540px"></div>
  <div class="abs social" style="left:558px"></div>
  <div class="abs social" style="left:576px"></div>
  <div class="abs social" style="left:594px"></div>
</footer>
</body>
</html>
```